Printed Circuit Board Company Web Site Design - Please see new file 82012 web design

We are a printed circuit board manufacturer. Need a company professional web site to allow our potential customers to know more about our background, capability and our products. The web site will contain three languages, which are Chinese, English and Japanese. Our audience are mainly electronic companies that procure printed circuit boards. I have a word document that have all the required text in all three languages. The final design should communicate the impression that we embrace quality, trustworthiness and long term partnership business principles.
We should have sections that allow us to post pictures of our facilities.
I have added the three files in three different languages.
Some of the information is below:
Background
RDV Harbourline Limited (RDV) was set up in Hong Kong in 2007 by two Hong Kong entrepreneurs, Mr. Tak Wong and Mr. Lok Fai. We acquired the single sided printed circuit board factory located in Dongguan City, Guangdong Province, China, from Tovand Corporation of the U.S. in 2007. In addition to RDV, Mr. Wong and Mr. Fai also own Halberd Technology Company Limited, a semiconductor company based in Hong Kong since 1997 with a total investment of over US$100 million. Halberd is engaged in the manufacturing of flexible substrates and MEMS assembly business.
RDV has been awarded TS 16949 and ISO14000 certificates since 2009 and 2004 respectively.
Business Principles
RDV Harbourline Limited strives to be a professional top notched printed circuit board supplier. We embrace four “EXCELLENCE” principles, namely, excellence in quality, excellence in prices, excellence in services and excellence in on time delivery.
We approach each customer with a long-term partnership view that delivers the lowest ownership costs and highest total values to our customers. We customize quotations and solutions in order to allow our customers to win more businesses. We believe by thinking from our customers’ points of view we will be able to create a WIN-WIN relationship.
Customers
Due to our excellent quality, services and production systems, RDV Harbourline Limited manage to service a number of large Japanese and US customers, which include:
Technical capability overview
Below is an overview of our current capability:
Target Market(s)
Electronic companies buyers
Industry/Entity Type
Business
Requirements
Must have
- Capability description
Should not have
- no cartoon

```html
<!DOCTYPE html>
<html lang="en">
<head>
<meta charset="utf-8">
<title>RDV Harbourline Limited</title>
<link href="https://fonts.googleapis.com/css2?family=Arimo:wght@400;700&family=Oswald:wght@300&display=swap" rel="stylesheet">
<style>
:root{
  --green:#128f6e;
  --green-dark:#0b7b5c;
  --green-light:#23a884;
  --text:#333333;
  --muted:#666666;
  --link:#1a4fa8;
  --footer:#222222;
  --footer-line:#3a3a3a;
  --footer-text:#bbbbbb;
  --white:#ffffff;
  --border:#cccccc;
}
*{margin:0;padding:0;box-sizing:border-box}
html,body{width:942px;height:1200px;overflow:hidden;background:var(--white)}
body{position:relative;font-family:"Arimo",Arial,sans-serif;color:var(--text)}
.abs{position:absolute}

.brand{left:70px;top:20px;display:flex;align-items:center;gap:8px;font-size:20px;font-weight:700;color:var(--green)}
.brand-mark{width:22px;height:22px;background:var(--green)}
.search{left:680px;top:11px;width:192px;height:22px;border:1px solid var(--border);border-radius:3px;font-size:11px;color:#888;padding:4px 8px}
.search svg{position:absolute;right:6px;top:5px}
.nav{left:352px;top:44px;display:flex;align-items:center;font-size:12px;font-weight:700;color:#333}
.nav a{color:inherit;text-decoration:none}
.nav .sep{margin:0 16px;font-weight:400}
.nav .active{background:var(--green-light);color:var(--white);border-radius:4px;padding:5px 16px;margin-right:-12px}

.banner{left:0;top:71px;width:942px;height:282px;background:linear-gradient(180deg,var(--green-dark),var(--green))}
.banner-photo{left:68px;top:6px;width:399px;height:268px;border:4px solid var(--white);background:linear-gradient(135deg,#8d9a94,#d8dcd6 55%,#5d6660)}
.arrow{width:46px;height:46px;border-radius:50%;background:#555;border:4px solid var(--white);top:117px;display:flex;align-items:center;justify-content:center}
.banner h2{left:493px;top:62px;font-size:22px;font-weight:700;color:var(--white)}
.banner p{left:493px;top:97px;width:350px;font-size:10.2px;line-height:14px;font-weight:700;color:var(--white)}
.learn{left:494px;top:196px;width:96px;height:27px;background:var(--white);border-radius:5px;font-size:12px;color:#333;display:flex;align-items:center;justify-content:center;gap:6px;box-shadow:0 1px 2px rgba(0,0,0,.3)}
.pager{left:420px;top:353px;width:98px;height:21px;background:#f2f2f2;border:1px solid #ddd;border-top:none;border-radius:0 0 4px 4px;display:flex;align-items:center;justify-content:center;gap:8px}
.pager i{width:7px;height:7px;border-radius:50%;background:#c8c8c8}
.pager i.on{background:#e08a2a}

.principles{left:67px;top:386px;width:806px;height:248px;border:1px solid var(--border)}
.principles h2{position:absolute;left:25px;top:24px;font-size:19px;font-weight:400}
.principles .copy{position:absolute;left:25px;top:69px;width:522px;font-size:9.8px;line-height:14px}
.principles .copy p+p{margin-top:14px}
.principles .photo{position:absolute;left:570px;top:57px;width:218px;height:151px;background:linear-gradient(180deg,#7c8894 0%,#c9cfd3 35%,#d2552c 40%,#c34a23 100%)}

.products h2{left:67px;top:656px;font-size:19px;font-weight:400}
.mini{width:17px;height:17px;border-radius:50%;background:#eee;border:1px solid #ddd;top:659px;font-size:10px;color:#888;display:flex;align-items:center;justify-content:center}
.product{top:695px;width:184px;text-align:center}
.product .ph{height:115px}
.product h3{margin-top:19px;font-size:11px;font-weight:700;color:var(--link)}
.product p{font-size:10px;line-height:14px;color:var(--text)}

.footer{left:0;top:913px;width:942px;height:287px;background:var(--footer)}
.col{top:32px;width:170px}
.col h4{font-family:"Oswald",sans-serif;font-weight:300;font-size:18px;color:#eee;padding-bottom:6px;border-bottom:1px solid var(--footer-line)}
.res li{list-style:none;font-size:10.5px;color:var(--footer-text);height:26px;display:flex;align-items:center;gap:10px}
.res{margin-top:14px}
.post{display:flex;gap:12px;margin-top:16px}
.post .th{width:45px;height:46px;border:2px solid #ddd;flex:none}
.post b{display:block;font-weight:400;font-size:10.5px;color:#ccc;margin-bottom:3px}
.post span{font-size:8.5px;line-height:14px;color:#aaa}
.social li{list-style:none;height:26px;display:flex;align-items:center;gap:12px;font-size:10px;color:#aaa}
.social{margin-top:14px}
.dot{width:20px;height:20px;border-radius:50%;background:#3a9fd8;border:2px solid #eee}
.field{height:21px;background:#2c2c2c;border:1px solid #333;font-size:8px;color:#aaa;padding:5px 9px;margin-top:6px}
.area{height:64px;background:#2c2c2c;border:1px solid #333;margin-top:6px}
.submit{width:48px;height:23px;background:#2c2c2c;border:1px solid #3a3a3a;font-size:8px;color:#ccc;display:flex;align-items:center;justify-content:center;margin-top:6px}
.bar{left:66px;top:231px;width:807px;height:43px;border-radius:5px;background:linear-gradient(180deg,var(--green-light),var(--green-dark));text-align:center;color:var(--white)}
.bar .links{margin-top:10px;font-size:9.5px}
.bar .links span{margin:0 4px}
.bar .copy{margin-top:3px;font-size:7.5px}
</style>
</head>
<body>

<div class="abs brand"><span class="brand-mark"></span>RDV Harbourline Limited</div>
<div class="abs search">Search
  <svg width="11" height="11" viewBox="0 0 11 11"><circle cx="6.5" cy="4.5" r="3.3" fill="none" stroke="#3a6bb0" stroke-width="1.4"/><line x1="4" y1="7" x2="1" y2="10" stroke="#3a6bb0" stroke-width="1.6"/></svg>
</div>
<nav class="abs nav">
  <a class="active" href="#">Home</a><span class="sep">|</span>
  <a href="#">About Us</a><span class="sep">|</span>
  <a href="#">Products</a><span class="sep">|</span>
  <a href="#">Principles</a><span class="sep">|</span>
  <a href="#">How it Works</a><span class="sep">|</span>
  <a href="#">Contact Us</a>
</nav>

<section class="abs banner">
  <div class="abs banner-photo" role="img" aria-label="Operator working at a circuit board processing line"></div>
  <div class="abs arrow" style="left:13px"><svg width="12" height="14"><path d="M9 2 L3 7 L9 12" stroke="#fff" stroke-width="3" fill="none"/></svg></div>
  <div class="abs arrow" style="left:883px"><svg width="12" height="14"><path d="M3 2 L9 7 L3 12" stroke="#fff" stroke-width="3" fill="none"/></svg></div>
  <h2 class="abs">Background</h2>
  <p class="abs">RDV Harbourline Limited (RDV) was set up in Hong Kong in 2007 by two HongKong entrepreneurs, Mr. Tak Wong and Mr. Lok Fai. We acquired the single sided printed circuit board factory located in Dongguan City, Guangdong Province, China, from Tovand Corporation of the U.S. in 2007.</p>
  <div class="abs learn">Learn More <svg width="5" height="8"><path d="M0 0 L5 4 L0 8Z" fill="#333"/></svg></div>
</section>
<div class="abs pager"><i class="on"></i><i></i><i></i><i></i><i></i></div>

<section class="abs principles">
  <h2>Business Principles</h2>
  <div class="copy">
    <p>RDV Harbourline Limited strives to be a professional top notched printed circuit board supplier. We embrace four “EXCELLENCE” principles, namely, excellence in quality, excellence in prices, excellence in services and excellence in on time delivery.</p>
    <p>We approach each customer with a long-term partnership view that delivers the lowest ownership costs and highest total values to our customers. We customize quotations and solutions in order to allow our customers to win more businesses. We believe by thinking from our customers’ points of view we will be able to create a WIN-WIN relationship.</p>
  </div>
  <div class="photo" role="img" aria-label="Orange production machines on the factory floor"></div>
</section>

<section class="products">
  <h2 class="abs">Our Products</h2>
  <div class="abs mini" style="left:833px">&lsaquo;</div>
  <div class="abs mini" style="left:854px">&rsaquo;</div>
  <div class="abs product" style="left:67px"><div class="ph" role="img" aria-label="Orange processing equipment" style="background:linear-gradient(180deg,#8894a0 0%,#cfd4d6 35%,#d2552c 40%,#b9b4aa 100%)"></div><h3>Lorem Lipsum</h3><p>Lorem Lipsum Dolor Sit Amet<br>of the private industry</p></div>
  <div class="abs product" style="left:273px"><div class="ph" role="img" aria-label="White board processing line" style="background:linear-gradient(135deg,#9aa2a2,#dcdedb 50%,#8f9896)"></div><h3>Lorem Lipsum</h3><p>Lorem Lipsum Dolor Sit Amet<br>of the private industry</p></div>
  <div class="abs product" style="left:479px"><div class="ph" role="img" aria-label="Control panels of a plating machine" style="background:linear-gradient(180deg,#5d636a,#c8ccce 40%,#9aa0a2 85%,#2a2a2a)"></div><h3>Lorem Lipsum</h3><p>Lorem Lipsum Dolor Sit Amet<br>of the private industry</p></div>
  <div class="abs product" style="left:687px"><div class="ph" role="img" aria-label="Interior of a stainless steel tank" style="background:radial-gradient(circle at 50% 40%,#dfe8e4,#7c948b 50%,#3c4a45)"></div><h3>Lorem Lipsum</h3><p>Lorem Lipsum Dolor Sit Amet<br>of the private industry</p></div>
</section>

<footer class="abs footer">
  <div class="abs col" style="left:71px">
    <h4>USEFUL RESOURCES</h4>
    <ul class="res">
      <li><span>&rsaquo;</span>Lorem ipsum Dolor Sit Amet</li>
      <li><span>&rsaquo;</span>Lorem ipsum Dolor Sit Amet</li>
      <li><span>&rsaquo;</span>Lorem ipsum Dolor Sit Amet</li>
      <li><span>&rsaquo;</span>Lorem ipsum Dolor Sit Amet</li>
      <li><span>&rsaquo;</span>Lorem ipsum Dolor Sit Amet</li>
    </ul>
  </div>
  <div class="abs col" style="left:267px">
    <h4>BLOG POSTS</h4>
    <div class="post"><div class="th" role="img" aria-label="Blog thumbnail in warm orange tones" style="background:linear-gradient(135deg,#f2a94a,#a8561c)"></div><div><b>Lorem Ipsum is simply</b><span>The printing and typesetting industry has been industry...</span></div></div>
    <div class="post"><div class="th" role="img" aria-label="Blog thumbnail of a sports field under blue sky" style="background:linear-gradient(180deg,#3f8ed8,#9fd0f0 50%,#4e9b2e 60%)"></div><div><b>Lorem Ipsum is simply</b><span>The printing and typesetting industry has been industry...</span></div></div>
  </div>
  <div class="abs col" style="left:461px">
    <h4>GET SOCIAL</h4>
    <ul class="social">
      <li><span class="dot"></span>Follow us on Chirpline</li>
      <li><span class="dot" style="background:#2d5ba8"></span>Friendship on Friendgrid</li>
      <li><span class="dot" style="background:#1d78b8"></span>Visit us on Worklink</li>
      <li><span class="dot" style="background:#3aaee0"></span>See our Vids on Clipreel</li>
      <li><span class="dot" style="background:#ef7a22"></span>Subscribe to RSS Feed</li>
    </ul>
  </div>
  <div class="abs col" style="left:654px">
    <h4>CONTACT US</h4>
    <div style="margin-top:12px">
      <div class="field">Name</div>
      <div class="field">Email</div>
      <div class="area"></div>
      <div class="submit">Submit</div>
    </div>
  </div>
  <div class="abs bar">
    <div class="links">Home<span>|</span>About Us<span>|</span>Products<span>|</span>Principles<span>|</span>How it Works<span>|</span>Contact Us</div>
    <div class="copy">© COPYRIGHTS 2012. ALL RIGHTS RESERVED.</div>
  </div>
</footer>

</body>
</html>
```